Awesome Business Card Design needed!

Hey there.
I'm looking for a simple but awesome business card design.
Type of company: Online advertisement agency
(please don't use the typical business people or statistics images on the card)
The front has to display the business name
and possibly some sort of logo ( perhaps something with the two M's of the biz name )
And the back of the card should say:
Name
Phone
Email
Let your imagination flow.
here are some designs that I like and that you can use as inspiration.
Simple but Awesome
http://images.lumavexo.com/designs/55128_877673_43091_thumbnail.jpg
http://images.lumavexo.com/designs/37714_747642_40106_image.jpg
http://images.lumavexo.com/designs/55128_877673_43091_image.jpg
http://images.lumavexo.com/designs/51321_781878_43091_image.jpg
http://images.lumavexo.com/designs/33378_399063_15912_image.jpg
http://images.lumavexo.com/designs/2337_271604_9495_image.jpg
good luck

```html
<!DOCTYPE html>
<html lang="en">
<head>
<meta charset="utf-8">
<title>Corvela Media – Business Cards</title>
<link rel="stylesheet" href="https://fonts.googleapis.com/css2?family=Archivo:wght@500;700;800&display=swap">
<style>
  :root {
    --page-bg: #d9d9db;
    --card-dark: #0c0c0e;
    --card-mid: #1b1c20;
    --brand-blue: #4a9be0;
    --silver: #d6d8dc;
    --text-light: #e4e6ea;
    --rule: #8a8d93;
  }
  * { margin: 0; padding: 0; box-sizing: border-box; }
  html, body {
    width: 1200px;
    height: 880px;
    overflow: hidden;
    background: var(--page-bg);
    font-family: "Archivo", Arial, sans-serif;
  }
  .sheet {
    width: 1200px;
    height: 880px;
    display: flex;
    align-items: center;
    justify-content: center;
    gap: 48px;
  }
  .card {
    position: relative;
    width: 540px;
    height: 310px;
    border-radius: 4px;
    overflow: hidden;
    box-shadow: 0 12px 30px rgba(0,0,0,0.35);
  }
  .card-texture {
    position: absolute;
    inset: 0;
    background: linear-gradient(150deg, var(--card-mid) 0%, var(--card-dark) 55%, var(--card-mid) 100%);
  }
  .card-content { position: relative; height: 100%; }

  /* front */
  .card-front .card-content {
    display: flex;
    flex-direction: column;
    align-items: center;
    justify-content: center;
    gap: 18px;
  }
  .brand-mark {
    width: 96px;
    height: 96px;
    background: var(--silver);
    border-radius: 2px;
  }
  .brand-name {
    font-weight: 800;
    font-size: 34px;
    letter-spacing: 1px;
    color: var(--brand-blue);
    text-transform: uppercase;
  }

  /* back */
  .card-back .card-content {
    padding: 44px 0 0 190px;
  }
  .back-brand {
    display: flex;
    align-items: center;
    gap: 12px;
    margin-bottom: 22px;
  }
  .back-brand .brand-mark { width: 44px; height: 44px; }
  .back-brand .brand-name { font-size: 24px; }
  .person-name {
    font-weight: 700;
    font-size: 22px;
    letter-spacing: 1px;
    color: var(--text-light);
    text-transform: uppercase;
    padding-bottom: 8px;
    border-bottom: 1px solid var(--rule);
    width: 260px;
    margin-bottom: 14px;
  }
  .contact-line {
    font-weight: 500;
    font-size: 14px;
    letter-spacing: 1px;
    color: var(--text-light);
    text-transform: uppercase;
    line-height: 1.8;
  }
</style>
</head>
<body>
  <main class="sheet">
    <section class="card card-front" aria-label="Business card front">
      <div class="card-texture" role="img" aria-label="Dark glossy embossed square pattern"></div>
      <div class="card-content">
        <div class="brand-mark"></div>
        <div class="brand-name">Corvela Media</div>
      </div>
    </section>

    <section class="card card-back" aria-label="Business card back">
      <div class="card-texture" role="img" aria-label="Dark glossy embossed square pattern"></div>
      <div class="card-content">
        <div class="back-brand">
          <div class="brand-mark"></div>
          <div class="brand-name">Corvela Media</div>
        </div>
        <div class="person-name">Daniel Hartley</div>
        <div class="contact-line">P: 1221 448 0917</div>
        <div class="contact-line">E: info@corvelamedia.com</div>
      </div>
    </section>
  </main>
</body>
</html>
```